Business Card Design

We are a commercial real estate brokerage in San Francisco, leasing office buildings downtown.
I would like a clean, elegant look. Simple but powerful .

Industry/Entity Type

Business

Contact Information for Business Card

Derek Holloway
lic# 07258143
415.555.0172
derek@velt-commercial.example
velt-commercial.example

```html
<!DOCTYPE html>
<html lang="en">
<head>
<meta charset="utf-8">
<title>VELT Commercial — Business Card</title>
<link rel="stylesheet" href="https://fonts.googleapis.com/css2?family=Arimo:wght@400;700&display=swap">
<style>
  :root {
    --page-bg: #e9eaed;
    --card-blue: #7d8dab;
    --card-white: #ffffff;
    --rule-grey: #8b8f96;
    --rule-light: #d4d7dc;
    --brand-slate: #6f7f9f;
    --skyline-tone-a: #5d6168;
    --skyline-tone-b: #a7abb2;
    --text-white: #ffffff;
    --text-soft: #eef1f7;
  }
  * { box-sizing: border-box; margin: 0; padding: 0; }
  html, body {
    width: 1200px; height: 950px; overflow: hidden;
    background: var(--page-bg);
    font-family: "Arimo", Arial, sans-serif;
  }
  .sheet {
    position: relative; width: 1200px; height: 950px;
    display: flex; flex-direction: column; align-items: center; justify-content: center; gap: 36px;
  }
  .card {
    position: relative; width: 760px; height: 434px; overflow: hidden;
    box-shadow: 0 6px 18px rgba(0,0,0,0.18);
  }

  /* Back side */
  .card-back { background: var(--card-blue); }
  .card-back .skyline {
    position: absolute; left: 250px; top: 78px; width: 260px; height: 170px;
  }
  .card-back .tagline {
    position: absolute; left: 0; right: 0; top: 282px;
    text-align: center; color: var(--text-white);
    font-size: 19px; line-height: 28px; letter-spacing: 0.2px;
  }

  /* Front side */
  .card-front { background: var(--card-white); }
  .front-band {
    position: absolute; left: 0; right: 0; top: 262px; bottom: 0;
    background: var(--card-blue);
    border-top: 5px solid var(--rule-grey);
    box-shadow: 0 -2px 0 var(--rule-light);
  }
  .brand {
    position: absolute; left: 170px; top: 100px;
    display: flex; align-items: center; gap: 22px;
  }
  .brand .skyline { width: 150px; height: 96px; }
  .brand-divider { width: 2px; height: 100px; background: var(--rule-grey); }
  .brand-name {
    color: var(--brand-slate); font-weight: 400;
    font-size: 56px; line-height: 1; letter-spacing: 1px;
  }
  .holder {
    position: absolute; left: 92px; top: 318px; color: var(--text-white);
  }
  .holder-name { font-weight: 700; font-size: 25px; }
  .holder-licence { font-size: 19px; margin-top: 8px; color: var(--text-soft); }
  .contacts {
    position: absolute; left: 400px; top: 292px; list-style: none;
    color: var(--text-white); font-size: 18px;
  }
  .contacts li { display: flex; align-items: center; gap: 12px; height: 30px; }
  .contacts svg { width: 18px; height: 18px; flex: none; }
</style>
</head>
<body>
<main class="sheet">

  <section class="card card-back" aria-label="Card back">
    <svg class="skyline" role="img" aria-label="Illustration of a downtown office skyline" viewBox="0 0 260 170">
      <defs>
        <linearGradient id="skyline-fill" x1="0" y1="0" x2="1" y2="1">
          <stop offset="0" stop-color="var(--skyline-tone-b)"/>
          <stop offset="1" stop-color="var(--skyline-tone-a)"/>
        </linearGradient>
      </defs>
      <rect x="0" y="0" width="260" height="170" rx="4" fill="url(#skyline-fill)"/>
    </svg>
    <p class="tagline">commercial real estate brokerage in San Francisco<br>leasing office buildings downtown.</p>
  </section>

  <section class="card card-front" aria-label="Card front">
    <div class="brand">
      <svg class="skyline" role="img" aria-label="Small downtown skyline illustration" viewBox="0 0 150 96">
        <defs>
          <linearGradient id="skyline-fill-small" x1="0" y1="0" x2="1" y2="1">
            <stop offset="0" stop-color="var(--skyline-tone-b)"/>
            <stop offset="1" stop-color="var(--skyline-tone-a)"/>
          </linearGradient>
        </defs>
        <rect x="0" y="0" width="150" height="96" rx="3" fill="url(#skyline-fill-small)"/>
      </svg>
      <span class="brand-divider"></span>
      <span class="brand-name">VELT Commercial</span>
    </div>

    <div class="front-band"></div>

    <div class="holder">
      <p class="holder-name">Derek Holloway</p>
      <p class="holder-licence">lic# 07258143</p>
    </div>

    <ul class="contacts">
      <li>
        <svg viewBox="0 0 18 18" aria-hidden="true"><path d="M3 6c0-2 2-3 6-3s6 1 6 3l-2 1.5-2-1.5h-4l-2 1.5z M5 9h8l2 6H3z" fill="var(--text-white)"/></svg>
        <span>415.555.0172</span>
      </li>
      <li>
        <svg viewBox="0 0 18 18" aria-hidden="true"><rect x="2" y="4" width="14" height="10" fill="var(--text-white)"/><path d="M2 4l7 6 7-6" fill="none" stroke="var(--card-blue)" stroke-width="1.4"/></svg>
        <span>derek@velt-commercial.example</span>
      </li>
      <li>
        <svg viewBox="0 0 18 18" aria-hidden="true"><circle cx="9" cy="9" r="7" fill="var(--text-white)"/><path d="M2 9h14M9 2c-3 3-3 11 0 14M9 2c3 3 3 11 0 14" fill="none" stroke="var(--card-blue)" stroke-width="1.2"/></svg>
        <span>velt-commercial.example</span>
      </li>
    </ul>
  </section>

</main>
</body>
</html>
```